BrivoTerna. Lantern of the Steady Harvest. Business card

Professional business card for BrivoTerna (Lantern of the Steady Harvest)
My rationale: Strategy-> Execution-> Results-> Value that lead to the BrivoTerna name: We put the Lantern of the Steady Harvest.
We deliver value to our customers helping them at defining a good strategy (cyan arrow). 90% of well formulated strategies fail due to poor execution so we also consider strategical execution very important (green arrow). Due to the execution we obtain the results (blue arrow). Finally, the results provide feedback to redefine strategy, and the new strategy has to be executed and new results obtained providing new feedback and on and on. It's like a wheel that finally, must create corporate value: value for shareholders, staholders, employees, providers...-

Target Market(s)

CEOs and steering comitees , invewrnent funds

Industry/Entity Type

Business Consultant

Contact Information for Business Card

Teodoro Vinsquel
CEO & Founder
teodoro.vinsquel@brivoterna-example.com
Mobile: +34 655.803.912
www.brivoterna-example.com

Colors

Designer to choose colors to be used in the design.

Requirements
Nice to have
• Nice to hace the words: Strategy, execution, results
• Nice to vave the claim: Lantern of the Steady Harvest
• The three colors should be shown:
• cyan for STRATEGY
• green for EXECUTION
• blue for RESULTS
Should not have
• Complete black background

```html
<!DOCTYPE html>
<html lang="en">
<head>
<meta charset="utf-8">
<title>BrivoTerna — Business Card</title>
<link rel="stylesheet" href="https://fonts.googleapis.com/css2?family=Open+Sans:wght@400;600;700&display=swap">
<style>
  :root {
    --backdrop: #ececec;
    --paper: #ffffff;
    --brand-navy: #003399;
    --brand-green: #8cc63f;
    --brand-cyan: #00aeef;
    --title-tint: #b3e6fb;
    --ink-light: #ffffff;
  }
  * { margin: 0; padding: 0; box-sizing: border-box; }
  html, body {
    width: 1200px;
    height: 851px;
    overflow: hidden;
    background: var(--backdrop);
    font-family: "Open Sans", Calibri, sans-serif;
  }
  .card {
    position: absolute;
    width: 405px;
    height: 232px;
  }
  .card--front {
    left: 168px;
    top: 310px;
    background: var(--paper);
  }
  .card--back {
    left: 628px;
    top: 309px;
    background: var(--brand-cyan);
    color: var(--ink-light);
    text-align: right;
  }
  .wordmark {
    position: absolute;
    left: 0;
    right: 0;
    top: 132px;
    text-align: center;
    font-size: 40px;
    font-weight: 700;
    letter-spacing: -1.5px;
    color: var(--brand-navy);
    line-height: 1;
  }
  .tagline {
    position: absolute;
    left: 0;
    right: 0;
    top: 199px;
    text-align: center;
    font-size: 10px;
    letter-spacing: 2px;
    line-height: 1;
  }
  .tagline__strategy { color: var(--brand-navy); }
  .tagline__execution { color: var(--brand-green); }
  .tagline__results { color: var(--brand-cyan); }
  .tagline__dot { color: var(--brand-navy); margin: 0 7px; }
  .holder {
    position: absolute;
    right: 19px;
    top: 16px;
  }
  .holder__name {
    font-size: 12.5px;
    font-weight: 700;
    line-height: 15px;
  }
  .holder__role {
    font-size: 11px;
    color: var(--title-tint);
    line-height: 14px;
  }
  .contact {
    position: absolute;
    right: 19px;
    top: 162px;
    list-style: none;
    font-size: 13px;
    line-height: 18.5px;
  }
</style>
</head>
<body>
  <section class="card card--front">
    <div class="wordmark">BrivoTerna</div>
    <p class="tagline">
      <span class="tagline__strategy">STRATEGY</span><span class="tagline__dot">·</span><span class="tagline__execution">EXECUTION</span><span class="tagline__dot">·</span><span class="tagline__results">RESULTS</span>
    </p>
  </section>

  <section class="card card--back">
    <div class="holder">
      <p class="holder__name">Teodoro VINSQUEL</p>
      <p class="holder__role">CEO &amp; Founder</p>
    </div>
    <ul class="contact">
      <li>+34 655 803 912</li>
      <li>teodoro.vinsquel@brivoterna-example.com</li>
      <li>www.brivoterna-example.com</li>
    </ul>
  </section>
</body>
</html>
```